K7 Electrical Services Ltd Web design

I require a web site for my new electrical contracting company. We are customer service orientated. Offering high value electrical installations, design and maintenance. Focused on custom residential and commercial upgrading. Lighting design and application are paramount in our company's services. Industry leading product use and integration are always on the forefront with our customer client services. As well as energy efficiency.

Target Market(s)

Homebuilders, General Contractors, Property management companies, clients, individuals,

Industry/Entity Type

Electric Company

Coding

Coded - Design and coding required

Number of Pages Required

3 page

Requirements
Must have
• Classic, modern, edgy but not trendy . Appeals to the masse.
• 3 page
• home page
• about page
• gallery page
• ability to contact from the webiste
Nice to have
• open to all types of designs that are relative to the construction industry.
• Black, Grey, metallic ice blue and deep purple colours from the logo.
Should not have
• anything cheesy with cartoon light bulb images.

```html
<!DOCTYPE html>
<html lang="en">
<head>
<meta charset="utf-8">
<title>K7 Electrical Services Ltd</title>
<link rel="stylesheet" href="https://fonts.googleapis.com/css2?family=Exo+2:wght@500;600;700&family=Open+Sans:wght@400;600&family=Roboto:wght@400;500&display=swap">
<style>
:root{
  --purple:#5b2a86;
  --purple-band:#6a3596;
  --ink:#333333;
  --text:#777777;
  --grey-light:#f4f4f6;
  --bar:#5a5a5a;
  --white:#ffffff;
}
*{margin:0;padding:0;box-sizing:border-box}
html,body{width:1200px;height:2605px;overflow:hidden}
body{position:relative;background:var(--white);font-family:"Open Sans",Arial,sans-serif;color:var(--text)}
.abs{position:absolute}
.heading{font-family:"Exo 2",Arial,sans-serif;font-weight:700;letter-spacing:1px;text-transform:uppercase}

/* header */
.site-header{left:0;top:0;width:1200px;height:101px;background:var(--white)}
.brand{left:87px;top:38px;font-family:"Open Sans",Arial,sans-serif;font-weight:600;color:var(--ink);font-size:18px;line-height:24px;white-space:nowrap}
.main-nav{top:45px;left:0;font-family:"Roboto",Arial,sans-serif;font-size:12px;font-weight:500;color:var(--ink);letter-spacing:.5px}
.main-nav a{position:absolute;white-space:nowrap;color:var(--ink);text-decoration:none}
.main-nav a.active{color:var(--purple)}
.search-btn{left:1060px;top:28px;width:52px;height:52px;border:2px solid var(--purple);border-radius:50%}

/* hero */
.hero{left:0;top:101px;width:1200px;height:505px;background:linear-gradient(180deg,#3e4758 0%,#6b5f6a 35%,#c97a45 62%,#5a3a2a 82%,#241a16 100%)}
.hero-title{left:87px;top:254px;font-size:42px;color:var(--white);letter-spacing:2px}
.hero-text{left:87px;top:318px;width:420px;font-size:11.5px;line-height:25px;color:var(--white)}
.btn-solid{left:87px;top:419px;width:148px;height:47px;background:var(--purple);color:var(--white);font-weight:600;font-size:15px;line-height:47px;text-align:center;border-radius:2px}

/* services */
.service{top:606px;width:400px;height:311px;text-align:center;background:linear-gradient(180deg,#fafafa,#eaeaec)}
.service.alt{background:linear-gradient(180deg,#e3e3e5,#ececee)}
.service svg{margin-top:40px}
.service h3{font-family:"Roboto",Arial,sans-serif;font-weight:500;font-size:18px;color:var(--ink);letter-spacing:1px;margin-top:14px}
.service p{width:290px;margin:12px auto 0;font-size:11.5px;line-height:25px}
.btn-outline{display:inline-block;margin-top:18px;width:105px;height:39px;border:1px solid var(--purple);color:var(--purple);font-size:12px;line-height:37px;background:var(--white)}

/* welcome */
.welcome-title{left:0;top:978px;width:1200px;text-align:center;font-size:25px;color:var(--purple)}
.welcome-intro{left:225px;top:1028px;width:750px;text-align:center;font-size:11px;line-height:26px}
.about-visual{left:87px;top:1150px;width:479px;height:311px;background:radial-gradient(ellipse at 45% 50%,#46525e 0%,#2b333c 60%,#1f252c 100%)}
.about-title{left:617px;top:1154px;font-size:17px;color:var(--purple)}
.about-text{left:617px;top:1205px;width:470px;font-size:11px;line-height:26px}

/* projects */
.projects{left:0;top:1522px;width:1200px;height:429px;background:var(--purple-band)}
.projects-title{left:0;top:1547px;width:1200px;text-align:center;font-size:25px;color:var(--white)}
.projects-sub{left:0;top:1588px;width:1200px;text-align:center;font-size:11.5px;color:var(--white)}
.project{top:1640px;width:330px;height:266px;background:var(--white)}
.project-photo{width:330px;height:210px}
.project h4{font-family:"Exo 2",Arial,sans-serif;font-weight:600;font-size:14.5px;color:var(--purple);text-align:center;line-height:56px;letter-spacing:1px;text-transform:uppercase}

/* testimonial */
.testimonial{left:0;top:1951px;width:1200px;height:321px;background:var(--grey-light)}
.quote-mark{font-family:Georgia,serif;font-size:36px;color:#bbbbbb;line-height:1}
.quote-text{left:219px;top:2044px;width:545px;font-size:11.5px;line-height:25px;color:#555}
.author{left:221px;top:2163px;font-family:"Roboto",Arial,sans-serif;font-weight:500;font-size:14px;color:var(--purple);letter-spacing:.5px}
.posted{left:221px;top:2186px;font-size:11.5px;color:#888}
.portrait{left:817px;top:2013px;width:196px;height:196px;border-radius:50%;border:5px solid #ddd;background:radial-gradient(circle at 50% 45%,#c99a82 0%,#8a5a42 55%,#cfd3d8 100%)}

/* footer */
.site-footer{left:0;top:2272px;width:1200px;height:269px;background:#f9f9fb}
.footer-brand{left:100px;top:2386px;width:250px;font-family:"Open Sans",Arial,sans-serif;font-weight:600;color:var(--ink);font-size:22px;line-height:30px}
.footer-head{font-family:"Roboto",Arial,sans-serif;font-weight:500;font-size:16px;color:var(--ink);letter-spacing:.5px}
.footer-text{font-size:11.5px;line-height:21px;color:#888}
.contact-item{left:394px;font-size:11.5px;color:#777;display:flex;align-items:flex-start;gap:12px;width:220px;line-height:17px}
.contact-item svg{flex:none;margin-top:1px}
.email-field{left:641px;top:2421px;width:214px;height:34px;border:1px solid #ccc;background:var(--white);font-size:11px;line-height:32px;padding-left:14px;color:#666}
.btn-subscribe{left:641px;top:2464px;width:82px;height:28px;background:var(--purple);color:var(--white);font-size:11px;line-height:28px;text-align:center}
.social{top:2451px;width:36px;height:36px;border:1px solid #bbb;border-radius:50%}
.copyright-bar{left:0;top:2541px;width:1200px;height:64px;background:var(--bar);color:var(--white);font-size:11.5px;text-align:center;line-height:56px}
</style>
</head>
<body>

<header class="site-header abs">
  <div class="brand abs">K7 Electrical Services Ltd</div>
  <nav class="main-nav abs">
    <a class="active" style="left:559px">HOME</a>
    <a style="left:648px">ABOUT US</a>
    <a style="left:767px">SERVICES</a>
    <a style="left:881px">NEWS</a>
    <a style="left:973px">CONTACT US</a>
  </nav>
  <div class="search-btn abs">
    <svg width="48" height="48" viewBox="0 0 48 48"><circle cx="23" cy="23" r="5" fill="none" stroke="#5b2a86" stroke-width="2"/><line x1="27" y1="27" x2="31" y2="31" stroke="#5b2a86" stroke-width="2"/></svg>
  </div>
</header>

<section class="hero abs" role="img" aria-label="Photo of electricity pylons against a sunset sky"></section>
<h1 class="hero-title heading abs">K7 Electrical</h1>
<p class="hero-text abs">Sed ut perspiciatis unde omnis iste natus error sit voluptatem accusantium doloremque laudantium, totam rem aperiam, eaque ipsa quae ab illo inven quasi architecto beatae vitae dicta sunt explicabo.</p>
<div class="btn-solid abs">READ MORE</div>

<section class="service abs" style="left:0">
  <svg width="90" height="64" viewBox="0 0 90 64" aria-hidden="true">
    <polygon points="45,2 4,32 14,32 45,10 76,32 86,32" fill="#5b2a86"/>
    <rect x="64" y="6" width="8" height="16" fill="#5b2a86"/>
    <rect x="16" y="30" width="58" height="32" fill="#666a70"/>
    <rect x="24" y="38" width="12" height="12" fill="#fff"/><rect x="54" y="38" width="12" height="12" fill="#fff"/>
    <rect x="40" y="42" width="10" height="20" fill="#fff"/>
  </svg>
  <h3>RESIDENTIAL</h3>
  <p>Sed ut perspiciatis unde omnis iste natus error sit voluptatem accusantium doloremque laudantium, eaque ipsa quae ab illo inventore</p>
  <span class="btn-outline">READ MORE</span>
</section>
<section class="service alt abs" style="left:400px">
  <svg width="90" height="64" viewBox="0 0 90 64" aria-hidden="true">
    <polygon points="24,8 60,2 60,62 24,62" fill="#666a70"/>
    <polygon points="60,2 70,8 70,62 60,62" fill="#5b2a86"/>
    <g fill="#fff"><rect x="29" y="14" width="8" height="6"/><rect x="42" y="12" width="8" height="6"/><rect x="29" y="26" width="8" height="6"/><rect x="42" y="24" width="8" height="6"/><rect x="29" y="38" width="8" height="6"/><rect x="42" y="36" width="8" height="6"/><rect x="29" y="50" width="8" height="6"/><rect x="42" y="48" width="8" height="6"/></g>
  </svg>
  <h3>COMMERCIAL</h3>
  <p>Sed ut perspiciatis unde omnis iste natus error sit voluptatem accusantium doloremque laudantium, eaque ipsa quae ab illo inventore</p>
  <span class="btn-outline">READ MORE</span>
</section>
<section class="service abs" style="left:800px">
  <svg width="90" height="64" viewBox="0 0 90 64" aria-hidden="true">
    <rect x="16" y="4" width="9" height="26" fill="#5b2a86"/><rect x="33" y="4" width="9" height="26" fill="#5b2a86"/><rect x="50" y="4" width="9" height="26" fill="#5b2a86"/>
    <polygon points="14,28 76,28 76,62 14,62" fill="#666a70"/>
    <g fill="#fff"><rect x="22" y="38" width="9" height="8"/><rect x="40" y="38" width="9" height="8"/><rect x="58" y="38" width="9" height="8"/><rect x="22" y="50" width="9" height="8"/><rect x="40" y="50" width="9" height="8"/><rect x="58" y="50" width="9" height="8"/></g>
  </svg>
  <h3>INDUSTRY</h3>
  <p>Sed ut perspiciatis unde omnis iste natus error sit voluptatem accusantium doloremque laudantium, eaque ipsa quae ab illo inventore</p>
  <span class="btn-outline">READ MORE</span>
</section>

<h2 class="welcome-title heading abs">Welcome to K7 Electrical</h2>
<p class="welcome-intro abs">Sed ut perspiciatis unde omnis iste natus error sit voluptatem accusantium doloremque laudantium, totam rem aperiam, eaque ipsa quae ab illo inventore veritatis et quasi architecto beatae vitae dicta sunt explicabo. Nemo enim ipsam voluptatem quia voluptas sit aspernatur sed quia consequuntur magni dolores eos qui ratione voluptatem sequi nesciunt.</p>
<div class="about-visual abs" role="img" aria-label="Company sign on a dark office wall"></div>
<h3 class="about-title heading abs">Sed ut perspiciatis unde omnis iste</h3>
<div class="about-text abs">
  <p>Sed ut perspiciatis unde omnis iste natus error sit voluptatem accusantium dolore mque laudantium, totam rem aperiam, eaque ipsa quae ab illo inventore veritatis et quasi architecto beatae vitae dicta sunt explicabo. Nemo enim ipsam voluptatem quia voluptas sit aspernatur sed quia consequuntur magni dolores eos qui ratione voluptatem sequi nesciunt.</p>
  <p style="margin-top:21px">Nemo enim ipsam voluptatem quia voluptas sit aspernatur aut odit aut fugit, sed quia consequuntur magni dolores eos qui ratione voluptatem sequi nesciunt.mque lauda ntium, totam rem aperiam, eaque ipsa quae</p>
</div>

<section class="projects abs"></section>
<h2 class="projects-title heading abs">Latest Projects</h2>
<p class="projects-sub abs">Sed ut perspiciatis unde omnis iste natus error sit voluptatem accusantium dolore mque laudantium,</p>
<article class="project abs" style="left:85px">
  <div class="project-photo" role="img" aria-label="Electrician testing a distribution board with a multimeter" style="background:linear-gradient(135deg,#8d9196,#c9b58a 50%,#4b4f55)"></div>
  <h4>Sed ut perspiciatis unde</h4>
</article>
<article class="project abs" style="left:435px">
  <div class="project-photo" role="img" aria-label="Bundle of colourful electrical cables" style="background:linear-gradient(135deg,#2c4f7a,#5b8fb8 45%,#b04a3a 75%,#1d2a3a)"></div>
  <h4>Sed ut perspiciatis unde</h4>
</article>
<article class="project abs" style="left:784px">
  <div class="project-photo" role="img" aria-label="Hand working on circuit breakers in a fuse box" style="background:linear-gradient(135deg,#7a2a25,#c9594a 45%,#d8d2c8 80%)"></div>
  <h4>Sed ut perspiciatis unde</h4>
</article>

<section class="testimonial abs"></section>
<span class="quote-mark abs" style="left:200px;top:2024px">&ldquo;</span>
<p class="quote-text abs">Sed ut perspiciatis unde omnis iste natus error sit voluptatem accusantium doloremque laudantium, totam rem aperiam, eaque ipsa quae ab illo inventore veritatis et quasi architecto beatae vitae dicta sunt explicabo. Nemo enim ipsam voluptatem quia voluptas sit aspernatur aut odit aut fugit, sed quia consequuntur magni dolores eos qui ratione voluptatem sequi nesciunt.</p>
<span class="quote-mark abs" style="left:604px;top:2138px">&rdquo;</span>
<p class="author abs">MARA QUINN</p>
<p class="posted abs">Posted On 07 Feb 2018</p>
<div class="portrait abs" role="img" aria-label="Portrait photo of a smiling client"></div>

<footer class="site-footer abs"></footer>
<div class="footer-brand abs">K7 Electrical<br>Services Ltd</div>

<h4 class="footer-head abs" style="left:394px;top:2324px">CONTACT US</h4>
<div class="contact-item abs" style="top:2368px">
  <svg width="14" height="14" viewBox="0 0 14 14"><rect x="1" y="5" width="12" height="8" rx="1" fill="#777"/><path d="M1 5 Q7 0 13 5" stroke="#777" stroke-width="2" fill="none"/></svg>
  <span>(000)-555-0142 (Phone)</span></div>
<div class="contact-item abs" style="top:2396px">
  <svg width="14" height="14" viewBox="0 0 14 14"><rect x="3" y="1" width="8" height="5" fill="none" stroke="#777"/><rect x="1" y="6" width="12" height="7" rx="1" fill="#777"/></svg>
  <span>(000)-555-0143 (Fax)</span></div>
<div class="contact-item abs" style="top:2424px">
  <svg width="14" height="14" viewBox="0 0 14 14"><rect x="1" y="3" width="12" height="9" fill="none" stroke="#777"/><path d="M1 3 L7 8 L13 3" fill="none" stroke="#777"/></svg>
  <span style="text-decoration:underline">info@k7electrical.com</span></div>
<div class="contact-item abs" style="top:2452px">
  <svg width="14" height="16" viewBox="0 0 14 16"><path d="M7 15 C3 9 2 7 2 5.5 A5 5 0 0 1 12 5.5 C12 7 11 9 7 15Z" fill="#777"/><circle cx="7" cy="5.5" r="1.8" fill="#fff"/></svg>
  <span>70 Lorem Ipsum Dummy Text Lorem Ipsum</span></div>

<h4 class="footer-head abs" style="left:641px;top:2324px">NEWSLETTER</h4>
<p class="footer-text abs" style="left:641px;top:2364px;width:210px">Register Your email address to get information about us</p>
<div class="email-field abs">Email Address</div>
<div class="btn-subscribe abs">SUBSCRIBE</div>

<h4 class="footer-head abs" style="left:894px;top:2326px">FOLLOW US</h4>
<p class="footer-text abs" style="left:894px;top:2364px;width:200px">Lorem ipsum dolor sit amet, conse ctetur adipiscing elit. Nulla in purus nibh. Donec ornare</p>
<span class="social abs" style="left:891px"></span>
<span class="social abs" style="left:934px"></span>
<span class="social abs" style="left:977px"></span>
<span class="social abs" style="left:1020px"></span>
<span class="social abs" style="left:1063px"></span>

<div class="copyright-bar abs">&copy; Copyright 2018 K7 Electrical.All Rights Reserved</div>

</body>
</html>
```